Business Cards Needed for Innovative Healthcare Marketing Company

We are a marketing company focused on healthcare. Our company is all about rebranding yourself renewing your image and generating results. The phoenix stands for "reborn" or "rising" which we provide new brands for our clients we take their old brands and renew it with creativity and innovation. I am looking for a business card with color dimension. I have attached an example of a card I think has the look and feel of what I am trying to accomplish. I like that the card example has black and grey font colors, I like the font placement and the small logo, I really like the use of the colors on the right those are the colors of my logo. My logo is phoenix so maybe incorporating flames similar to that design. I would like the back a solid color maybe red with an opaque version of the logo and website. As a marketing company I am always open to creative liberty!

Target Market(s)

Doctors and business professionals.

Industry/Entity Type

Marketing

Contact Information for Business Card

Valcorne Health Care Marketing
Marla Tenwick- CEO
#(512)638-2974
email-marla@valcorne.com
website- valcorne.com

Font styles to use
Sans Serif

Colors
ec1f27
f37122
ffc214
fbed22
fbf289
f04a50

Requirements
Must have
• The logo and required information
Nice to have
• icons by the information
Should not have
• child like font

```html
<!DOCTYPE html>
<html lang="en">
<head>
<meta charset="utf-8">
<title>Valcorne Health Care Marketing — Business Card</title>
<link href="https://fonts.googleapis.com/css2?family=Raleway:wght@300;400;500&display=swap" rel="stylesheet">
<style>
  :root {
    --stage: #ecebe8;
    --card-white: #ffffff;
    --brand-red: #a51d27;
    --brand-red-dark: #8e1820;
    --brand-orange: #f37122;
    --brand-yellow: #ffc214;
    --logo-red: #c0474a;
    --text-white: #ffffff;
  }
  * { margin: 0; padding: 0; box-sizing: border-box; }
  html, body {
    width: 1200px; height: 950px; overflow: hidden;
    background: var(--stage);
    font-family: "Raleway", sans-serif;
  }
  .stage {
    position: relative; width: 1200px; height: 950px;
  }
  .card {
    position: absolute; width: 700px; height: 400px;
    border-radius: 26px; overflow: hidden;
    box-shadow: 0 8px 24px rgba(0,0,0,0.18);
  }
  .card-front { left: 250px; top: 50px; background: var(--card-white); }
  .card-back { left: 250px; top: 500px; background: var(--brand-red); }

  .front-shapes { position: absolute; inset: 0; }

  .brand {
    position: absolute; left: 120px; top: 62px;
    display: flex; align-items: center; gap: 22px;
  }
  .brand-mark {
    width: 74px; height: 74px; border-radius: 50%;
    background: var(--logo-red);
  }
  .brand-name {
    color: var(--logo-red); font-weight: 300;
    letter-spacing: 3px; line-height: 1.05;
  }
  .brand-name .primary { display: block; font-size: 46px; }
  .brand-name .secondary { display: block; font-size: 14px; letter-spacing: 4px; margin-top: 6px; }

  .person {
    position: absolute; left: 70px; top: 300px;
    display: flex; align-items: baseline; gap: 26px;
  }
  .person-name { color: var(--brand-orange); font-size: 27px; font-weight: 500; letter-spacing: 0.5px; }
  .person-title { color: var(--text-white); font-size: 20px; font-weight: 400; }

  .contact-list {
    position: absolute; left: 420px; top: 226px;
    list-style: none; color: var(--text-white);
    font-size: 19px; font-weight: 400; letter-spacing: 1px;
  }
  .contact-list li { display: flex; align-items: center; gap: 12px; height: 32px; }
  .contact-icon { width: 16px; height: 16px; flex: none; }

  .back-site {
    position: absolute; left: 60px; top: 200px;
    transform: translate(-50%, -50%) rotate(90deg);
    color: var(--text-white); font-size: 15px; letter-spacing: 6px; font-weight: 400;
    white-space: nowrap; margin-left: 10px;
  }
  .back-brand {
    position: absolute; left: 0; right: 0; top: 0; bottom: 0;
    display: flex; align-items: center; justify-content: center; gap: 20px;
  }
  .back-brand .brand-mark { background: var(--text-white); width: 60px; height: 60px; }
  .back-brand .brand-name { color: var(--text-white); font-size: 44px; }
</style>
</head>
<body>
<main class="stage">
  <section class="card card-front" aria-label="Business card front">
    <svg class="front-shapes" width="700" height="400" viewBox="0 0 700 400">
      <defs>
        <linearGradient id="redBand" x1="0" y1="0" x2="1" y2="0">
          <stop offset="0" stop-color="#b53a42"/>
          <stop offset="0.35" stop-color="var(--brand-red)"/>
          <stop offset="1" stop-color="var(--brand-red-dark)"/>
        </linearGradient>
        <linearGradient id="flameLine" x1="0" y1="0" x2="1" y2="0">
          <stop offset="0" stop-color="var(--brand-yellow)"/>
          <stop offset="1" stop-color="var(--brand-orange)"/>
        </linearGradient>
      </defs>
      <path class="red-band" d="M0 262 C 200 250, 430 200, 700 150 L700 400 L0 400 Z" fill="url(#redBand)"/>
      <path class="flame-swoosh" d="M20 262 C 220 246, 420 204, 600 168 C 470 204, 260 250, 20 262 Z" fill="url(#flameLine)" stroke="url(#flameLine)" stroke-width="3"/>
    </svg>

    <div class="brand">
      <span class="brand-mark"></span>
      <span class="brand-name">
        <span class="primary">VALCORNE</span>
        <span class="secondary">HEALTH CARE MARKETING</span>
      </span>
    </div>

    <div class="person">
      <span class="person-name">MARLA TENWICK</span>
      <span class="person-title">CEO</span>
    </div>

    <ul class="contact-list">
      <li>
        <svg class="contact-icon" viewBox="0 0 16 16"><path d="M3 1 L6 1 L7 5 L5 6.5 C6 9 7 10 9.5 11 L11 9 L15 10 L15 13 C15 14 14 15 13 15 C6 14.5 1.5 10 1 3 C1 2 2 1 3 1 Z" fill="var(--brand-orange)"/></svg>
        (512)638-2974
      </li>
      <li>
        <svg class="contact-icon" viewBox="0 0 16 16"><rect x="1" y="3" width="14" height="10" rx="1.5" fill="var(--brand-orange)"/><path d="M1.5 4 L8 9 L14.5 4" fill="none" stroke="var(--brand-red)" stroke-width="1.3"/></svg>
        marla@valcorne.com
      </li>
      <li>
        <svg class="contact-icon" viewBox="0 0 16 16"><circle cx="8" cy="8" r="7" fill="var(--brand-orange)"/><path d="M1 8 H15 M8 1 C4 5 4 11 8 15 M8 1 C12 5 12 11 8 15" fill="none" stroke="var(--brand-red)" stroke-width="1"/></svg>
        www.valcorne.com
      </li>
    </ul>
  </section>

  <section class="card card-back" aria-label="Business card back">
    <span class="back-site">www.valcorne.com</span>
    <div class="back-brand">
      <span class="brand-mark"></span>
      <span class="brand-name">VALCORNE</span>
    </div>
  </section>
</main>
</body>
</html>
```